RTavenor Business Cards & Letterhead

I have a logo but need a design for some new business cards. We are a Design-Build Firm that specializes in the design and construction of commercial projects.
the cards need to be professional. no cartoon stuff.
i would like to have the cards in AI format so I can update the card as needed. Logo is provided.
Our Address is: 4187 Marlowe Ct. Elmrow, South Vandale 27614

```html
<!DOCTYPE html>
<html lang="en">
<head>
<meta charset="utf-8">
<title>RTavenor Business Card</title>
<link rel="stylesheet" href="https://fonts.googleapis.com/css2?family=Montserrat:wght@800&family=Open+Sans:wght@400;600;700&display=swap">
<style>
  :root {
    --backdrop: #4a4a4a;
    --card-black: #141414;
    --deep-black: #0a0a0a;
    --brand-blue: #1a78c2;
    --edge-blue: #1d5fb8;
    --text-white: #ffffff;
    --mark-grey: #5e5e5e;
  }
  * { margin: 0; padding: 0; box-sizing: border-box; }
  html, body {
    width: 1200px; height: 801px; overflow: hidden;
    background: var(--backdrop);
  }
  .stage {
    position: relative; width: 1200px; height: 801px;
    display: flex; align-items: center; justify-content: center; gap: 40px;
  }
  .card {
    position: relative; width: 530px; height: 303px;
    border-radius: 16px; overflow: hidden;
    background: var(--card-black);
    border: 2px solid var(--edge-blue);
    box-shadow: 0 14px 30px rgba(0,0,0,.45);
  }
  /* front */
  .brand {
    position: absolute; left: 38px; top: 36px;
    display: flex; align-items: center; gap: 10px;
    z-index: 1;
  }
  .brand-square { width: 22px; height: 22px; background: var(--brand-blue); }
  .brand-name {
    font-family: "Montserrat", sans-serif; font-weight: 800;
    font-size: 31px; letter-spacing: .5px; color: var(--text-white);
  }
  .side-bar {
    position: absolute; left: 0; top: 94px; width: 18px; height: 34px;
    background: var(--brand-blue);
  }
  .person { position: absolute; left: 38px; top: 94px; font-family: "Open Sans", sans-serif; }
  .person-name { font-weight: 700; font-size: 19px; color: var(--brand-blue); letter-spacing: .5px; }
  .person-role { font-size: 14px; color: var(--text-white); margin-top: 1px; }
  .contacts {
    position: absolute; left: 38px; top: 160px; list-style: none;
    font-family: "Open Sans", sans-serif; font-size: 13.5px; color: var(--text-white);
  }
  .contacts li { display: flex; align-items: center; gap: 8px; line-height: 20px; }
  .contacts svg { width: 11px; height: 11px; fill: var(--brand-blue); flex: none; }
  .address {
    position: absolute; left: 38px; top: 236px;
    font-family: "Open Sans", sans-serif; font-size: 13.5px; line-height: 20px;
    color: var(--text-white); font-style: normal;
  }
  .front-decor {
    position: absolute; left: 318px; top: 52px; width: 184px; height: 196px;
    border-radius: 32px;
    background: linear-gradient(135deg, #2e2e2e 0%, #111 45%, #070707 100%);
    box-shadow: inset 0 0 0 1px rgba(255,255,255,.04);
  }
  /* back */
  .card-back .pattern {
    position: absolute; inset: 0;
    background: linear-gradient(135deg, #0d4f8c 0%, #1a7fd0 30%, #0b0b0b 50%, #1a7fd0 70%, #0d4f8c 100%);
  }
  .back-name {
    position: absolute; left: 0; right: 0; top: 50%; transform: translateY(-50%);
    text-align: center;
    font-family: "Montserrat", sans-serif; font-weight: 800;
    font-size: 54px; letter-spacing: 1px; color: var(--mark-grey);
  }
</style>
</head>
<body>
<main class="stage">
  <section class="card card-front">
    <div class="front-decor" role="img" aria-label="Large glossy black brand emblem decoration"></div>
    <div class="brand">
      <span class="brand-square"></span>
      <span class="brand-name">RTAVENOR</span>
    </div>
    <span class="side-bar"></span>
    <div class="person">
      <p class="person-name">OWEN HARTLEY</p>
      <p class="person-role">Managing Director</p>
    </div>
    <ul class="contacts">
      <li><svg viewBox="0 0 24 24"><path d="M6.6 10.8a15 15 0 0 0 6.6 6.6l2.2-2.2c.3-.3.7-.4 1-.2 1.1.4 2.3.6 3.6.6.6 0 1 .4 1 1V20c0 .6-.4 1-1 1A17 17 0 0 1 3 4c0-.6.4-1 1-1h3.5c.6 0 1 .4 1 1 0 1.3.2 2.5.6 3.6.1.3 0 .7-.2 1z"/></svg>123 456 789</li>
      <li><svg viewBox="0 0 24 24"><path d="M2 5h20v14H2z M2 5l10 8 10-8" /></svg>info@youremail.com</li>
      <li><svg viewBox="0 0 24 24"><circle cx="12" cy="12" r="10"/></svg>www.yourwebsite.com</li>
    </ul>
    <address class="address">4187 Marlowe Ct. Elmrow,<br>South Vandale 27614</address>
  </section>

  <section class="card card-back">
    <div class="pattern" role="img" aria-label="Repeating blue brand emblem pattern on black"></div>
    <p class="back-name">RTAVENOR</p>
  </section>
</main>
</body>
</html>
```